Design a calming beauty medical salon & spa website based in Hong Kong

We need help building an informational website for a beauty salon in Hong Kong. The local salon provides facials, massages, body and other slimming treatments in a relaxing environment. We offer some non-invasive medical treatments, such as botox. Having built the business on word of mouth, it is now time for us to launch a website to help market the business better. Website requirements:

-Must be responsive
-Use vibrant but clean colours. not too many, 1-2 colours
-Must be bilingual (switch between Chinese traditional and English)
-Our current website is host on a server, not using any particular platforms like wordpress

Pages:
1/ Homepage
2/ About us (incorporate gallery of salon photos and history of company)
3/ Promotions and latest deals (and leads them to sign up for more info, maybe pop-up small window when you click on a promotion)
4/ Treatment menus
4.1/Body treatments
4.2/ Face treatments
4.3/ Slimming treatments
5/ Showcasing products sold (no e-commerce functionality, just showing off products)
6/ Contact us (tel, address, map, opening hrs)

Footer - must haves include contact us info, privacy policy, terms & conditions, copyright blurb, join our company/employment page (with a form)

For information (comparable websites we like):
http://veltora.com/
http://pambrix.com.hk/tc/aboutpambrix/background.php#centerenvi
Attaching a very first draft concept for this website
Attaching pictures of the beauty salon
Attaching logo

Target Market(s)

Hong Kong based, Chinese, females, 30-50+ age. 90% female clients.

Industry/Entity Type

Beauty Salon

Number of Pages Required

5+ page

Font styles to use
Sans Serif

Colors
f9d9e8
fbd3d4
fee3d5
fbe7d2
fee18a
fbf289
ffffff

Requirements
Must have
• interactive elements on website, such as scrolling banner photo headers
• incorporate photos of website salon
• connect to facebook page

```html
<!DOCTYPE html>
<html lang="en">
<head>
<meta charset="utf-8">
<title>Serene Bloom – Excellent Medical Beauty</title>
<link href="https://fonts.googleapis.com/css2?family=Kaushan+Script&family=Caveat+Brush&family=Lora:ital@1&family=Montserrat:wght@500;600&family=Roboto:wght@400;500&display=swap" rel="stylesheet">
<style>
:root{
  --purple:#6a1b7d;
  --header:#faf0f0;
  --hero:#f2dada;
  --rose:#f0b2b8;
  --text:#555;
  --dark:#333;
  --grey-bg:#f5f5f7;
  --yellow:#fde08a;
  --gold:#f5c842;
  --button:#3a3a3a;
  --white:#fff;
}
*{margin:0;padding:0;box-sizing:border-box}
html,body{width:786px;height:1200px;overflow:hidden;background:var(--white)}
body{position:relative;font-family:"Roboto",sans-serif;color:var(--text)}
.abs{position:absolute}
.hero{left:0;top:0;width:786px;height:384px;background:var(--hero)}
.hero-photo{left:64px;top:0;width:416px;height:384px;background:radial-gradient(ellipse at 45% 45%,#f3d0c2 0%,#e9bfb0 45%,#f2dada 78%)}
.header{left:0;top:0;width:786px;height:71px;background:rgba(250,240,240,.85)}
.brand{left:56px;top:14px;display:flex;align-items:center;gap:6px;font-family:"Kaushan Script",cursive;font-size:22px;color:var(--purple)}
.brand-dot{width:30px;height:30px;border-radius:50%;border:3px solid var(--purple)}
.contact-top{left:580px;top:8px;font-family:"Montserrat",sans-serif;font-size:7px;font-weight:500;color:#333;line-height:13px}
.contact-top svg{position:absolute;left:-22px;top:4px}
.lang{left:682px;top:8px;display:flex;border:1px solid #ddd;background:#fff}
.lang span{width:24px;height:20px;font-family:"Montserrat",sans-serif;font-size:7px;display:flex;align-items:center;justify-content:center}
.lang .on{color:var(--gold);border-right:1px solid #ddd}
.nav{left:281px;top:45px;display:flex;gap:18px;font-family:"Montserrat",sans-serif;font-size:7.4px;font-weight:600;color:#222;text-transform:uppercase}
.hero-brand{left:456px;top:140px;display:flex;align-items:center;gap:10px;font-family:"Kaushan Script",cursive;font-size:36px;color:var(--purple)}
.hero-brand .brand-dot{width:56px;height:56px;border-width:5px}
.tagline{left:456px;top:228px;width:250px;text-align:center;font-family:"Lora",serif;font-style:italic;font-size:18px;color:#555}
.title{width:786px;left:0;text-align:center;font-family:"Kaushan Script",cursive;font-size:21px;color:var(--rose)}
.intro{left:155px;top:454px;width:476px;text-align:center;font-size:7.2px;line-height:17.5px;color:#555}
.service{width:180px;text-align:center;top:538px}
.service .pic{width:128px;height:128px;margin:0 auto;border-radius:50%;border:3px solid #eee}
.service h3{margin-top:20px;font-family:"Caveat Brush",cursive;font-weight:400;font-size:19px;color:#444}
.contact{left:0;top:732px;width:786px;height:342px;background:var(--grey-bg)}
.info{left:95px;font-size:9.5px;line-height:18.5px;color:#555}
.info svg{position:absolute;left:0;top:3px}
.info p{margin-left:22px}
.hotline{display:flex;gap:14px}
.hotline b{font-size:12px;font-weight:500;color:#444}
.map{left:392px;top:809px;width:338px;height:234px;border:1px solid #ddd;padding:3px;background:#fff}
.map div{width:100%;height:100%;background:linear-gradient(160deg,#efe9dc 0%,#e6e0d2 45%,#cfe3c4 60%,#9fc7ef 75%,#efe9dc 90%)}
.join{left:0;top:1074px;width:786px;height:78px;background:var(--yellow)}
.join-label{left:60px;top:1099px;font-family:"Kaushan Script",cursive;font-size:15px;color:#fff}
.join-input{left:276px;top:1098px;width:328px;height:29px;background:#fff;border:1px solid #eee;font-size:7.5px;color:#444;padding:11px 0 0 11px}
.join-btn{left:614px;top:1098px;width:91px;height:29px;background:var(--button);color:#fff;font-family:"Caveat Brush",cursive;font-size:15px;display:flex;align-items:center;justify-content:center}
.footer{left:0;top:1152px;width:786px;height:48px;background:var(--dark)}
.copy{left:57px;top:1171px;font-size:8.5px;color:#fff}
.copy u{margin:0 9px}
.social{left:593px;top:1166px;display:flex;gap:4px}
.social span{width:24px;height:24px;border-radius:50%;border:1.5px solid #fff}
</style>
</head>
<body>
<div class="abs hero"></div>
<div class="abs hero-photo" role="img" aria-label="Portrait of a woman touching her cheek, soft skin-care photo"></div>
<div class="abs header"></div>

<div class="abs brand"><span class="brand-dot"></span>Serene Bloom</div>
<div class="abs contact-top">
  <svg width="14" height="14" viewBox="0 0 14 14"><circle cx="7" cy="7" r="6" fill="none" stroke="#f5c842" stroke-width="1.6"/><path d="M5 5c0 2 2 4 4 4" stroke="#f5c842" stroke-width="1.4" fill="none"/></svg>
  TEL: 2618 4470<br>WHATSAPP: 6390 2157
</div>
<div class="abs lang"><span class="on">EN</span><span>CN</span></div>
<nav class="abs nav"><span>Home</span><span>About us</span><span>Promotions &amp; latest deals</span><span>Treatment</span><span>Products showcase</span><span>Contact us</span></nav>

<div class="abs hero-brand"><span class="brand-dot"></span>Serene Bloom</div>
<div class="abs tagline">Excellent Medical Beauty</div>

<h2 class="abs title" style="top:415px">All For Beauty Services</h2>
<p class="abs intro">To take care of all aspects of the skin different needs, providing facial and body care, Customers can enjoy a more efficient and beautiful skin treatment in a relaxed and comfortable environment. Together with the noble Swiss brand Serene Bloom organic material series for home care, In order to push the quality of skin to the pinnacle.</p>

<div class="abs service" style="left:80px"><div class="pic" role="img" aria-label="Facial mask treatment photo" style="background:radial-gradient(circle at 40% 45%,#e9c4b0,#8a5a3c 70%,#3a2418)"></div><h3>Facial Care</h3></div>
<div class="abs service" style="left:305px"><div class="pic" role="img" aria-label="Back massage photo" style="background:radial-gradient(circle at 50% 50%,#d79a6c,#b8713f 70%,#8d4f28)"></div><h3>Body Care</h3></div>
<div class="abs service" style="left:530px"><div class="pic" role="img" aria-label="Slimming device treatment photo" style="background:radial-gradient(circle at 50% 40%,#d8c2b2,#6f5c52 65%,#2e2826)"></div><h3>Slim Body</h3></div>

<div class="abs contact"></div>
<h2 class="abs title" style="top:750px">Contact Us</h2>

<div class="abs info" style="top:837px">
  <svg width="10" height="10" viewBox="0 0 10 10"><circle cx="5" cy="5" r="4" fill="none" stroke="#888" stroke-width="1.2"/><path d="M5 2.5V5h2" stroke="#888" stroke-width="1.1" fill="none"/></svg>
  <p>Monday to Friday: 10:30 am to 9:30 pm<br>Saturday and holidays: 10:30 am to 7:30 pm</p>
</div>
<div class="abs info" style="top:888px">
  <svg width="10" height="10" viewBox="0 0 10 10"><path d="M2 1l2 2-1 1.5c.6 1.2 1.3 1.9 2.5 2.5L7 6l2 2-1.5 1.5C4.5 9 1 5.5.5 2.5z" fill="#888"/></svg>
  <p class="hotline"><b>Inquiry Hotline :</b><span>26184470<br>63902157</span></p>
</div>
<div class="abs info" style="top:942px">
  <svg width="10" height="11" viewBox="0 0 10 11"><path d="M5 10S1.5 6 1.5 4a3.5 3.5 0 0 1 7 0C8.5 6 5 10 5 10z" fill="#888"/><circle cx="5" cy="4" r="1.3" fill="#f5f5f7"/></svg>
  <p>12th Floor, Silver Lotus Tower, 21-23 Harbour Lane<br>Tsim Sha Tsui, Kowloon</p>
</div>
<div class="abs info" style="top:994px">
  <svg width="11" height="9" viewBox="0 0 11 9"><rect x=".6" y=".6" width="9.8" height="7.8" fill="none" stroke="#888" stroke-width="1.1"/><path d="M.6.6l4.9 4 4.9-4" fill="none" stroke="#888" stroke-width="1.1"/></svg>
  <p style="margin-left:25px">hello@serenebloom.hk</p>
</div>
<div class="abs map"><div role="img" aria-label="Street map showing the salon location"></div></div>

<div class="abs join"></div>
<div class="abs join-label">Join Our Company/Employment :</div>
<div class="abs join-input">Enter Email id :</div>
<div class="abs join-btn">JOIN US</div>

<div class="abs footer"></div>
<div class="abs copy">Copyright © 2018 Serene Bloom HK Ltd. All rights reserved. <u style="margin:0">Privacy Policy</u><span style="margin:0 12px">|</span><u style="margin:0">Terms &amp; Conditions</u></div>
<div class="abs social" aria-label="Social links"><span></span><span></span><span></span><span></span><span></span></div>
</body>
</html>
```